Corvane Capital Business Cards

These are professional business cards that are for my family office.
Put fake emails and phone numbers as of now until I finalize those components. This family office controls my families investments, assets, and future. The cards should be professional.
..
.
.
.
I just uploaded another variation of a logo I would like to see as a business card to I am inbeteen which logo to use

Target Market(s)

business

Industry/Entity Type

business

Contact Information for Business Card

Professional, wealth related, finance related.

Requirements
Must have
• Logo

```html
<!DOCTYPE html>
<html lang="en">
<head>
<meta charset="utf-8">
<title>Corvane Capital Business Cards</title>
<link rel="stylesheet" href="https://fonts.googleapis.com/css2?family=Tinos:wght@400;700&display=swap">
<style>
  :root {
    --page: #f2f2f2;
    --navy: #1b2d57;
    --gold: #c5ac6e;
    --ink: #1c1c1c;
    --white: #ffffff;
  }
  * { margin: 0; padding: 0; box-sizing: border-box; }
  html, body { width: 1200px; height: 1200px; overflow: hidden; }
  body { background: var(--page); font-family: "Tinos", "Times New Roman", serif; position: relative; }

  .card {
    position: absolute; left: 270px; width: 660px; height: 377px;
    background: var(--navy); border-radius: 19px; overflow: hidden;
  }
  .card-front { top: 197px; }
  .card-back { top: 626px; }

  .tab { position: absolute; top: 110px; width: 42px; height: 157px; background: var(--gold); }
  .tab-left { left: 0; border-radius: 0 6px 6px 0; }
  .tab-right { right: 0; border-radius: 6px 0 0 6px; }

  .brand-name {
    position: absolute; left: 0; right: 0; text-align: center;
    color: var(--gold); font-weight: 400; letter-spacing: 1px; text-transform: uppercase;
    white-space: nowrap;
  }
  .card-front .brand-name { top: 160px; font-size: 44px; }
  .card-back .brand-name { left: 40px; width: 300px; right: auto; top: 190px; font-size: 27px; letter-spacing: 0.5px; }

  .divider { position: absolute; left: 362px; top: 59px; width: 3px; height: 133px; background: var(--white); border-radius: 2px; }

  .row { position: absolute; left: 394px; right: 0; display: flex; }
  .row-icon { width: 52px; background: var(--ink); display: flex; align-items: center; justify-content: center; }
  .row-icon svg { width: 20px; height: 20px; }
  .row-body { flex: 1; background: var(--white); color: var(--ink); font-size: 13px; padding-left: 27px; display: flex; align-items: center; }

  .name-row { top: 52px; height: 42px; }
  .name-row .row-body { background: var(--gold); flex-direction: column; align-items: flex-start; justify-content: center; line-height: 1; }
  .person-name { font-size: 20px; color: var(--white); }
  .person-name strong { color: var(--ink); font-weight: 700; }
  .person-role { font-size: 12px; color: var(--white); margin-top: 1px; }

  .phone-row { top: 132px; height: 29px; }
  .email-row { top: 175px; height: 28px; }
  .web-row { top: 217px; height: 29px; }

  .address { position: absolute; left: 478px; top: 293px; display: flex; align-items: center; gap: 10px; color: var(--white); }
  .address svg { width: 20px; height: 20px; }
  .address p { font-size: 12.5px; line-height: 13px; }
</style>
</head>
<body>
  <section class="card card-front">
    <div class="tab tab-left"></div>
    <div class="tab tab-right"></div>
    <h1 class="brand-name">Corvane Capital</h1>
  </section>

  <section class="card card-back">
    <h2 class="brand-name">Corvane Capital</h2>
    <div class="divider"></div>

    <div class="row name-row">
      <div class="row-icon">
        <svg viewBox="0 0 20 20" fill="#fff"><circle cx="10" cy="5" r="4"/><path d="M2 20v-5c0-3 2-5 5-5h6c3 0 5 2 5 5v5z"/><path d="M9 10h2l-1 7z" fill="#1c1c1c"/></svg>
      </div>
      <div class="row-body">
        <div class="person-name"><strong>Daniel</strong> Mercer</div>
        <div class="person-role">Manager</div>
      </div>
    </div>

    <div class="row phone-row">
      <div class="row-icon">
        <svg viewBox="0 0 20 20" fill="none" stroke="#fff" stroke-width="1.6" stroke-linecap="round"><path d="M4 3l3 0 1.5 4-2 1.5c1 2.2 2.8 4 5 5l1.5-2 4 1.5v3c0 1-1 2-2 2C8 18 2 12 2 5c0-1 1-2 2-2z"/><path d="M12 2a6 6 0 0 1 6 6M12 5a3 3 0 0 1 3 3"/></svg>
      </div>
      <div class="row-body">0100 555 0142</div>
    </div>

    <div class="row email-row">
      <div class="row-icon">
        <svg viewBox="0 0 20 20" fill="none" stroke="#fff" stroke-width="1.5"><rect x="2" y="4.5" width="16" height="11"/><path d="M2 4.5l8 6 8-6M2 15.5l6-5M18 15.5l-6-5"/></svg>
      </div>
      <div class="row-body">office@corvanemail.com</div>
    </div>

    <div class="row web-row">
      <div class="row-icon">
        <svg viewBox="0 0 20 20" fill="none" stroke="#fff" stroke-width="1.4"><circle cx="10" cy="10" r="8"/><path d="M2 10h16M10 2c-3 3-3 13 0 16M10 2c3 3 3 13 0 16"/><path d="M11 11l6 2.5-2.5 1 2 2.5-1 .8-2-2.5-1.5 2z" fill="#fff" stroke="#1c1c1c" stroke-width="0.8"/></svg>
      </div>
      <div class="row-body">www.corvanecapital.com</div>
    </div>

    <div class="address">
      <svg viewBox="0 0 20 20" fill="none" stroke="#fff" stroke-width="2" stroke-linejoin="round"><path d="M2 10L10 3l8 7"/><path d="M4.5 8.5V18h11V8.5"/><rect x="8" y="12" width="4" height="6" fill="#fff" stroke="none"/></svg>
      <p>Your location<br>Harbor Lane, Eastport,<br>2045.</p>
    </div>
  </section>
</body>
</html>
```